Fine Art business needs new website

We need a simple website with a home page, about us page, New sculptures, Sold sculptures, and a contact us page.Our sculptures are very high end one of a kind pieces. As such we need the site to be VERY elegant and professional. Lastly, because I'll be updating pictures on the website on a monthly basis it needs to be user friendly to update (Wordpress is preferred). The only branding we have so far for the business is a business card.
Updates
I wasn't completely ready when this project launched, also I am on the road right now and haven't been able to be as responsive to all you designers as I would like. I will work on giving feedback to all the top designs we've received so far. Thank you all so much for your participation and hardwork.
Target Market(s)
High end customers (affluent), art collectors, interior decorators/designers
Industry/Entity Type
Art Gallery
Coding
Coded - Design and coding required
Number of Pages Required
5+ page
Requirements
Must have
- Easily editable picture gallery for myself so that I can add new pieces(pictures of the pieces), remove sold pieces, etc. I would like the website to be built in wordpress so I can update it. I currently use mangewordpress through Netmarro for my other business website and would like to do the same for this one.
- Pages:
- -Intro page with featured pieces
- -Current pieces gallery (for sale) mainly a picture gallery
- -Sculptures archive (sold pieces) another picture gallery
- -About us: Pull-down of -about the artist (attached content)
- -Artistic Process (attached content)
- -Show Schedule:
- -one page dedicated to "friends of TMV" (basically a link page)
- TO BE CLEAR "www.pineroverslane.com" IS A TOTALLY DIFFERENT SITE AND I'M NOT TRYING TO COMBINE THE TWO OR JOIN THEM INTO ONE. This page needs be more elegant and seperate from the Pine Rovers site.
- UPDATE: I'd like a link to the TMV Faceplume page: https://www.faceplume-social.com/mirelcraftworks/
Nice to have
- I would like the pictures on the gallery pages able to have text connected with them (Materials, price)
- I would like the site style and fonts to be similar to our business cards we've already had designed (picture attached).
Should not have
- Too much flash or other things that will make the site slow to load.

```html
<!DOCTYPE html>
<html lang="en">
<head>
<meta charset="utf-8">
<title>Mirelcraft Works – Contact Us</title>
<link href="https://fonts.googleapis.com/css2?family=EB+Garamond:ital,wght@0,400;0,500;1,700&family=Arimo:wght@400;700&display=swap" rel="stylesheet">
<style>
  :root {
    --ink: #4a4a4a;
    --ink-soft: #666666;
    --paper: #ffffff;
    --map-light: #efefef;
    --map-tone: #e3e7ea;
    --field-line: #cfcfcf;
    --button: #555555;
    --footer: #1c1c1c;
    --footer-base: #0c0c0c;
    --footer-text: #f2f2f2;
    --footer-rule: #6a6a6a;
    --card-mark: #8a8a8a;
  }
  * { margin: 0; padding: 0; box-sizing: border-box; }
  html, body { width: 937px; height: 1200px; overflow: hidden; background: var(--paper); }
  body { position: relative; font-family: "EB Garamond", Georgia, serif; color: var(--ink); }
  .abs { position: absolute; }

  .site-title { top: 16px; left: 0; width: 937px; text-align: center; font-size: 28px; letter-spacing: 1px; color: var(--ink); line-height: 36px; font-weight: 400; }
  .main-nav { top: 70px; left: 0; width: 937px; display: flex; justify-content: center; gap: 23px; font-size: 9px; letter-spacing: 0; line-height: 14px; }
  .main-nav a { color: var(--ink); text-decoration: none; }
  .main-nav a.current { border-bottom: 1.5px solid var(--ink); padding-bottom: 2px; }

  .page-heading { top: 162px; left: 0; width: 937px; text-align: center; font-size: 48px; font-weight: 400; letter-spacing: 1px; line-height: 60px; color: #555; }

  .location-map { top: 261px; left: 0; width: 937px; height: 275px;
    background: linear-gradient(100deg, var(--map-light) 0%, var(--map-tone) 45%, var(--map-light) 100%); }

  .section-heading { top: 583px; left: 0; width: 937px; text-align: center; font-size: 18px; letter-spacing: .5px; line-height: 24px; font-weight: 400; }

  .contact-details { top: 633px; left: 200px; width: 219px; text-align: right; font-size: 14px; line-height: 17.5px; color: var(--ink-soft); font-style: normal; }
  .contact-details p { margin-bottom: 16px; }

  .contact-form .field { position: absolute; left: 451px; width: 242px; border: 1px solid var(--field-line); background: var(--paper); font-size: 6px; color: #aaa; padding: 3px 8px; }
  .field-name { top: 636px; height: 17px; }
  .field-email { top: 662px; height: 17px; }
  .field-message { top: 690px; height: 87px; padding-top: 7px !important; }
  .send-button { top: 790px; left: 451px; width: 43px; height: 17px; background: var(--button); color: #fff; font-size: 6.5px; text-align: center; line-height: 17px; }

  .site-footer { top: 878px; left: 0; width: 937px; height: 296px; background: var(--footer); }
  .footer-base { top: 1174px; left: 0; width: 937px; height: 26px; background: var(--footer-base); color: #888; font-size: 6.5px; text-align: center; line-height: 26px; }

  .footer-heading { top: 906px; font-size: 14px; font-weight: 400; letter-spacing: .3px; line-height: 18px; color: var(--footer-text); }
  .footer-text { font-size: 9px; line-height: 14px; color: var(--footer-text); }
  .show-date { font-style: italic; font-weight: 700; font-size: 9px; color: var(--footer-text); }
  .footer-rule { height: 1px; background: var(--footer-rule); }
  .footer-link { font-size: 9px; text-decoration: underline; color: var(--footer-text); }

  .post-card { left: 480px; width: 142px; height: 72px; background: #fff; border: 1px solid #ccc; color: #222; font-family: "Arimo", Arial, sans-serif; }
  .post-card .avatar { position: absolute; left: 4px; top: 4px; width: 18px; height: 18px; background: #9a9a9a; }
  .post-card .author { position: absolute; left: 28px; top: 5px; font-size: 6.5px; font-weight: 700; }
  .post-card .time { position: absolute; left: 28px; top: 14px; font-size: 4.5px; color: #999; }
  .post-card .mark { position: absolute; right: 5px; top: 5px; width: 8px; height: 8px; background: var(--card-mark); }
  .post-card .body { position: absolute; left: 5px; top: 27px; right: 5px; font-size: 6px; line-height: 9px; }

  .social-row { top: 1022px; left: 654px; display: flex; gap: 3px; }
  .social-row span { width: 10px; height: 10px; background: #fff; border-radius: 1px; }

  .newsletter-input { top: 1094px; left: 654px; width: 116px; height: 17px; border: 1px solid #ddd; background: var(--footer); }
  .newsletter-send { top: 1094px; left: 770px; width: 43px; height: 17px; background: #fff; color: #222; font-size: 6.5px; text-align: center; line-height: 17px; }
</style>
</head>
<body>
  <header>
    <h1 class="abs site-title">MIRELCRAFT WORKS</h1>
    <nav class="abs main-nav">
      <a href="#">HOME</a>
      <a href="#">ABOUT US</a>
      <a href="#">CURRENT PIECES</a>
      <a href="#">SCULPTURES ARCHIVE</a>
      <a href="#">PINEROVERS</a>
      <a href="#" class="current">CONTACT US</a>
    </nav>
  </header>

  <main>
    <h2 class="abs page-heading">CONTACT US</h2>

    <div class="abs location-map" role="img" aria-label="Grey street map of the city and harbour with the studio location marked"></div>

    <h3 class="abs section-heading">GET IN TOUCH WITH US</h3>

    <address class="abs contact-details">
      <p>The Pine Rovers<br>PO box 402118<br>Alder Falls CO 80999</p>
      <p>hollis@thepinerovers.com</p>
      <p>+1.5550142236</p>
    </address>

    <form class="contact-form">
      <div class="field field-name">Name</div>
      <div class="field field-email">Email</div>
      <div class="field field-message">Message</div>
      <div class="abs send-button">Send</div>
    </form>
  </main>

  <footer>
    <div class="abs site-footer"></div>

    <h4 class="abs footer-heading" style="left:125px">UPCOMING SHOWS</h4>
    <div class="abs footer-text" style="left:125px;top:949px">Art Fair Cedar Hollow</div>
    <div class="abs show-date" style="left:125px;top:964px">August 2018</div>
    <div class="abs footer-text" style="left:125px;top:989px">Larkspur Fine Art Show</div>
    <div class="abs show-date" style="left:125px;top:1004px">July 2018</div>
    <div class="abs footer-text" style="left:125px;top:1029px">Wrenfield Park Arts and<br>Music Festival</div>
    <div class="abs show-date" style="left:125px;top:1058px">June 2018</div>
    <div class="abs footer-text" style="left:125px;top:1082px">Marlow Creek Festival</div>
    <div class="abs show-date" style="left:125px;top:1097px">May 2018</div>
    <div class="abs footer-rule" style="left:125px;top:1117px;width:137px"></div>
    <a class="abs footer-link" style="left:125px;top:1124px" href="#">View All</a>

    <h4 class="abs footer-heading" style="left:296px">UPCOMING EVENTS</h4>
    <div class="abs footer-text" style="left:296px;top:949px">There are no upcoming events yet</div>
    <div class="abs footer-rule" style="left:296px;top:970px;width:138px"></div>
    <a class="abs footer-link" style="left:296px;top:984px" href="#">View Calender</a>

    <h4 class="abs footer-heading" style="left:480px">FACEPLUME</h4>
    <article class="abs post-card" style="top:952px">
      <div class="avatar" role="img" aria-label="Profile photo"></div>
      <div class="author">The Pine Rovers</div>
      <div class="time">10 hours ago</div>
      <div class="mark"></div>
      <div class="body">Geode fans, announcing a flash sale, free shipping on all Craftory orders for the next two weeks!!*<br>*Minimum $25 order</div>
    </article>
    <article class="abs post-card" style="top:1036px">
      <div class="avatar" role="img" aria-label="Profile photo"></div>
      <div class="author">The Pine Rovers</div>
      <div class="time">about a week ago</div>
      <div class="mark"></div>
      <div class="body">Few more new products. First a crystal canyon geode, then a THUNDEREGG! Both will be available on our Craftory store in the next week.</div>
    </article>
    <div class="abs footer-rule" style="left:480px;top:1122px;width:139px"></div>
    <a class="abs footer-link" style="left:480px;top:1134px" href="#">Goto Faceplume Page</a>

    <h4 class="abs footer-heading" style="left:653px">CONTACT US</h4>
    <div class="abs footer-text" style="left:653px;top:949px;line-height:11px">The Pine Rovers, PO box 402118<br>Alder Falls CO 80999</div>
    <div class="abs footer-text" style="left:653px;top:980px">hollis@thepinerovers.com</div>
    <div class="abs footer-text" style="left:653px;top:1000px">+1.5550142236</div>
    <div class="abs social-row" aria-label="Social links"><span></span><span></span><span></span><span></span><span></span><span></span></div>
    <div class="abs footer-rule" style="left:654px;top:1048px;width:139px"></div>
    <h4 class="abs footer-heading" style="left:654px;top:1068px">NEWSLETTER</h4>
    <div class="abs newsletter-input"></div>
    <div class="abs newsletter-send">Send</div>

    <div class="abs footer-base">Copyright © 2016 The Pine Rovers</div>
  </footer>
</body>
</html>
```